Business Card Design Project

This is the first time we use our new logo. We need a business card that we can use both on our institutional corporate relationships and also that works for our staff that deals with consumers directly.

VELUNDA is a new company dedicated to empower consumers and to provide them with the best choices for specialized health care using the latest telemedicine technology (medicine at a distance via videoconference).

We want to print this cards in high quality materials and process. We will like designs that allow us to use UV spot varnish and other techniques that will differentiate us.

We are including Two different versions of Color logos. In addition we are including white over black background logos. Those can be used replacing the black for a color.

Please note this is the first time we will be creating any corporate materials with our new logo and colors.

Target Market(s)

34+ consumers of medium high and high socioeconomic levels.

Industry/Entity Type

Health

Requirements
Must have
• Our logo on its original colors
Should not have
• Any other graphical element or design that is not our logo

```html
<!DOCTYPE html>
<html lang="en">
<head>
<meta charset="utf-8">
<title>VELUNDA Business Cards</title>
<link href="https://fonts.googleapis.com/css2?family=Jost:wght@400;500;600&display=swap" rel="stylesheet">
<style>
  :root {
    --backdrop: #7a5538;
    --label: #1c130c;
    --brand-navy: #1f5a86;
    --brand-blue: #2a7cc4;
    --brand-teal: #22a39a;
    --brand-sky: #5fb3df;
    --card-black: #050505;
    --silver-light: #e4e4e4;
    --silver-mid: #bdbdbd;
    --silver-dark: #3a3a3a;
    --ink-dark: #2a2a2a;
    --paper: #ffffff;
    --back-blue: #1e5a86;
  }
  * { box-sizing: border-box; margin: 0; padding: 0; }
  html, body { width: 1200px; height: 788px; overflow: hidden; }
  body {
    background: var(--backdrop);
    font-family: "Jost", "Futura", sans-serif;
    position: relative;
  }
  .sheet-label {
    position: absolute;
    font-size: 21px;
    color: var(--label);
    transform: translateX(-50%);
  }
  .card {
    position: absolute;
    width: 526px;
    height: 302px;
    border-radius: 22px;
    overflow: hidden;
  }
  .card--front { left: 53px; top: 73px; background: linear-gradient(100deg, var(--silver-mid), var(--silver-light) 40%, #cfcfcf 70%, var(--silver-mid)); }
  .card--back-white { left: 622px; top: 73px; background: var(--paper); }
  .card--back-metal { left: 53px; top: 445px; background: linear-gradient(180deg, #f0f0f0 0%, #c9c9c9 35%, #8a8a8a 70%, var(--silver-dark) 100%); }
  .card--back-blue { left: 622px; top: 445px; background: var(--back-blue); }

  .front-sweep { position: absolute; inset: 0; }

  .brand { position: absolute; display: flex; align-items: center; }
  .brand__dot { border-radius: 50%; background: var(--brand-teal); flex: none; }
  .brand__name { font-weight: 600; letter-spacing: 2px; line-height: 1; }

  .card--front .brand { left: 20px; top: 70px; width: 230px; flex-direction: column; gap: 22px; }
  .card--front .brand__dot { width: 64px; height: 64px; }
  .card--front .brand__name { font-size: 40px; color: var(--brand-navy); }

  .address {
    position: absolute; left: 0; width: 280px; top: 242px;
    text-align: center; font-size: 13.5px; line-height: 18px; color: var(--ink-dark);
  }

  .holder { position: absolute; left: 358px; top: 69px; color: var(--paper); }
  .holder__name { font-size: 18px; font-weight: 600; }
  .holder__role { font-size: 13px; }

  .contacts { position: absolute; left: 356px; top: 192px; list-style: none; color: var(--paper); font-size: 13.5px; }
  .contacts li { display: flex; align-items: center; height: 22px; }
  .contacts svg { width: 12px; height: 12px; margin-right: 10px; fill: var(--paper); }

  .card--back-white .brand { left: 96px; top: 95px; gap: 24px; }
  .card--back-white .brand__dot { width: 80px; height: 80px; }
  .card--back-white .brand__name { font-size: 48px; color: var(--brand-navy); }

  .card--back-metal .brand { left: 100px; top: 92px; gap: 24px; }
  .card--back-metal .brand__dot { width: 80px; height: 80px; }
  .card--back-metal .brand__name { font-size: 48px; color: var(--brand-navy); }

  .card--back-blue .brand { left: 0; right: 0; top: 30px; flex-direction: column; gap: 36px; }
  .card--back-blue .brand__dot { width: 86px; height: 86px; background: var(--brand-sky); }
  .card--back-blue .brand__name { font-size: 48px; color: var(--paper); }

  .web {
    position: absolute; left: 0; right: 0; bottom: 18px; text-align: center;
    font-size: 16px; letter-spacing: 3px;
  }
  .card--back-white .web { color: var(--ink-dark); }
  .card--back-metal .web, .card--back-blue .web { color: var(--paper); }
</style>
</head>
<body>
  <span class="sheet-label" style="left:320px; top:32px;">Front</span>
  <span class="sheet-label" style="left:896px; top:32px;">Back - 1</span>
  <span class="sheet-label" style="left:320px; top:404px;">Back - 2</span>
  <span class="sheet-label" style="left:896px; top:404px;">Back - 3</span>

  <section class="card card--front">
    <svg class="front-sweep" viewBox="0 0 526 302" preserveAspectRatio="none" aria-hidden="true">
      <path d="M322 0 C228 60 222 238 342 302 L526 302 L526 0 Z" fill="var(--brand-blue)"/>
      <path d="M336 0 C244 70 246 232 354 302 L526 302 L526 0 Z" fill="var(--card-black)"/>
    </svg>
    <div class="brand">
      <span class="brand__dot"></span>
      <span class="brand__name">VELUNDA</span>
    </div>
    <p class="address">#0000, Street Name<br>Area Name, Country Code</p>
    <div class="holder">
      <p class="holder__name">Your Name</p>
      <p class="holder__role">Designation</p>
    </div>
    <ul class="contacts">
      <li><svg viewBox="0 0 12 12"><path d="M3 1 L5 3.5 L4 5 C5 7 6 8 7.5 8.5 L9 7.5 L11 9.5 L9.5 11 C5 10.5 1.5 7 1 2.5 Z"/></svg>+10 555 01234</li>
      <li><svg viewBox="0 0 12 12"><path d="M2.5 4 L3.5 1.5 H8.5 L9.5 4 H11 V9 H9.5 V10.5 H8 V9 H4 V10.5 H2.5 V9 H1 V4 Z"/></svg>+10 555 01234</li>
      <li><svg viewBox="0 0 12 12"><path d="M1 2.5 H11 V10 H1 Z M1.8 3.3 L6 6.8 L10.2 3.3 Z" fill-rule="evenodd"/></svg>hello@velundahealth.com</li>
      <li><svg viewBox="0 0 12 12"><path d="M6 1 A5 5 0 1 0 6.01 1 Z M6 2 A4 4 0 1 1 5.99 2 Z M5.5 1.5 H6.5 V10.5 H5.5 Z M1.5 5.5 H10.5 V6.5 H1.5 Z" fill-rule="evenodd"/></svg>www.velundahealth.com</li>
    </ul>
  </section>

  <section class="card card--back-white">
    <div class="brand">
      <span class="brand__dot"></span>
      <span class="brand__name">VELUNDA</span>
    </div>
    <p class="web">www.velundahealth.com</p>
  </section>

  <section class="card card--back-metal">
    <div class="brand">
      <span class="brand__dot"></span>
      <span class="brand__name">VELUNDA</span>
    </div>
    <p class="web">www.velundahealth.com</p>
  </section>

  <section class="card card--back-blue">
    <div class="brand">
      <span class="brand__dot"></span>
      <span class="brand__name">VELUNDA</span>
    </div>
    <p class="web">www.velundahealth.com</p>
  </section>
</body>
</html>
```